Business cards for a fun web development agency

Hi,I am building a web development agency. You can read about it on the website http://kite-loft.examplehost.com. Basically, I want to focus on free and open source products and stay as far away from the corporate business feeling as possible. I want to build a community so I want the business card to feel fun and approachable (at the risk of professional if need be). I am uploading some of my image assets in various file formats. Feel free to use them or make your own if you want just keeping in theme with the website.
Industry/Entity Type
Building
Contact Information for Business Card
Company Name: Boat ShedWebsite: www.kiteloftdev.example (it's currently in alpha on http://kite-loft.examplehost.com if you want to see the them we are trying to capture)My name is: Banner B. SchaferMy email: banner@boatsheddev.comMy phone: 0431 587 904
Look and feel

```html
<!DOCTYPE html>
<html lang="en">
<head>
<meta charset="utf-8">
<title>Kite Loft — Business Cards</title>
<link rel="stylesheet" href="https://fonts.googleapis.com/css2?family=Roboto:wght@300;400&display=swap">
<style>
  :root {
    --page-bg: #e9ecef;
    --card-white: #fbfbfb;
    --brand-blue: #1a9bbf;
    --stripe-black: #1d1d1f;
    --logo-slate: #5b80a8;
    --ink: #2b2b2b;
    --rule: #b9bcc0;
  }
  * { box-sizing: border-box; margin: 0; padding: 0; }
  html, body { width: 1200px; height: 892px; overflow: hidden; }
  body {
    background: var(--page-bg);
    font-family: "Roboto", Arial, sans-serif;
    display: flex;
    flex-direction: column;
    align-items: center;
    justify-content: center;
    gap: 40px;
  }
  .card {
    position: relative;
    width: 700px;
    height: 400px;
    background: var(--card-white);
    overflow: hidden;
    box-shadow: 0 6px 18px rgba(0,0,0,0.18);
  }
  .card-bands { position: absolute; inset: 0; }
  .band { fill: url(#bandFill); }
  .stripe { fill: var(--stripe-black); }
  .stripe-white { fill: #ffffff; }

  .wordmark {
    display: flex;
    align-items: center;
    gap: 14px;
    color: var(--logo-slate);
    font-weight: 400;
    letter-spacing: 1px;
    white-space: nowrap;
  }
  .wordmark-dot {
    border-radius: 50%;
    background: var(--brand-blue);
    flex: none;
  }

  /* Front */
  .front-main {
    position: absolute;
    left: 80px;
    right: 90px;
    top: 112px;
    display: flex;
    align-items: flex-end;
    justify-content: space-between;
    gap: 24px;
    padding-bottom: 14px;
    border-bottom: 1px solid var(--rule);
  }
  .front-main .wordmark { font-size: 48px; }
  .front-main .wordmark-dot { width: 38px; height: 38px; }
  .holder-name {
    color: var(--logo-slate);
    font-size: 28px;
    font-weight: 400;
    white-space: nowrap;
    padding-bottom: 6px;
  }
  .contact-list {
    position: absolute;
    right: 90px;
    top: 200px;
    list-style: none;
    display: grid;
    grid-template-columns: auto 20px;
    column-gap: 14px;
    row-gap: 10px;
    align-items: center;
  }
  .contact-item { display: contents; }
  .contact-text {
    color: var(--ink);
    font-size: 16px;
    font-weight: 300;
    text-align: right;
    white-space: nowrap;
  }
  .contact-icon { width: 20px; height: 20px; display: block; }
  .contact-icon * { fill: none; stroke: var(--ink); stroke-width: 1.5; }

  /* Back */
  .back-logo {
    position: absolute;
    inset: 0;
    display: flex;
    align-items: center;
    justify-content: center;
  }
  .back-logo .wordmark { font-size: 74px; gap: 20px; }
  .back-logo .wordmark-dot { width: 60px; height: 60px; }
</style>
</head>
<body>

<svg width="0" height="0" style="position:absolute" aria-hidden="true">
  <defs>
    <linearGradient id="bandFill" x1="0" y1="0" x2="1" y2="1">
      <stop offset="0" stop-color="#23aacb"/>
      <stop offset="1" stop-color="#0f7fa6"/>
    </linearGradient>
  </defs>
</svg>

<section class="card card-front" aria-label="Business card front">
  <svg class="card-bands" viewBox="0 0 700 400" aria-hidden="true">
    <polygon class="band" points="0,0 110,0 0,160"/>
    <polygon class="stripe-white" points="110,0 124,0 0,180 0,160"/>
    <polygon class="stripe" points="124,0 133,0 0,193 0,180"/>
    <polygon class="band" points="700,400 600,400 700,255"/>
    <polygon class="stripe-white" points="600,400 586,400 700,235 700,255"/>
    <polygon class="stripe" points="586,400 577,400 700,222 700,235"/>
  </svg>

  <div class="front-main">
    <div class="wordmark"><span class="wordmark-dot"></span><span>KITE LOFT</span></div>
    <h1 class="holder-name">Corwin T. Aldous</h1>
  </div>

  <ul class="contact-list">
    <li class="contact-item">
      <span class="contact-text">0431 587 904</span>
      <svg class="contact-icon" viewBox="0 0 20 20"><circle cx="10" cy="10" r="9"/><path d="M7 5.5c-1 1-1 3 1.5 6s5 3.5 6 2.5l-1.5-1.8-1.6.8c-1-.5-2.5-2-3-3l.8-1.6z"/></svg>
    </li>
    <li class="contact-item">
      <span class="contact-text">www.kiteloftdev.example</span>
      <svg class="contact-icon" viewBox="0 0 20 20"><circle cx="10" cy="10" r="9"/><rect x="5" y="6" width="10" height="7" rx="1"/><path d="M8 15.5h4"/></svg>
    </li>
    <li class="contact-item">
      <span class="contact-text">corwin@kiteloftdev.example</span>
      <svg class="contact-icon" viewBox="0 0 20 20"><circle cx="10" cy="10" r="9"/><rect x="5" y="6.5" width="10" height="7"/><path d="M5 6.5l5 4 5-4"/></svg>
    </li>
  </ul>
</section>

<section class="card card-back" aria-label="Business card back">
  <svg class="card-bands" viewBox="0 0 700 400" aria-hidden="true">
    <polygon class="band" points="0,0 120,0 0,170"/>
    <polygon class="stripe" points="120,0 130,0 0,184 0,170"/>
    <polygon class="band" points="700,400 560,400 700,200"/>
    <polygon class="stripe" points="560,400 550,400 700,186 700,200"/>
  </svg>
  <div class="back-logo">
    <div class="wordmark"><span class="wordmark-dot"></span><span>KITE LOFT</span></div>
  </div>
</section>

</body>
</html>
```